Brintel Works - Fast, Efficient and Gas Mainteance for Domestic, Commercial and Industrial clients

We are in the process of purchasing a new business and would like to get a new logo and business card.
Business is a gas maintenance business that also does new gas installations.
Has been established since 1988.
Services include:
Install all types of gas appliances & equipment inc. hot water units
Maintain / repair / replace all types of gas appliances & equipment

Target Market(s)

Domestic, Commercial and Industrial clients

Industry/Entity Type

Business

Contact Information for Business Card

admin@brintelworks.com.au
07 3918 4726
Brintel Works PTY LTD

Logo Text

Gas Fitting & Plumbing Maintenance Specialists

Font styles to use
Sans Serif

Requirements
Must have
• Logo
• Business name, contact number, email address, web address
• Domestic | Commercial | Industrial Est Since 1988
Nice to have
• Possibly a black card with a flame logo to one side
Should not have
• Spelling errors

```html
<!DOCTYPE html>
<html lang="en">
<head>
<meta charset="utf-8">
<title>Brintel Works – Business Card</title>
<link rel="stylesheet" href="https://fonts.googleapis.com/css2?family=Archivo:wdth,wght@125,800&family=Montserrat:wght@400;500;600&display=swap">
<style>
  :root {
    --page: #ece8e3;
    --card: #050505;
    --white: #ffffff;
    --text: #e9e9e9;
    --orange: #f07f22;
    --amber: #f6a21f;
    --red: #ee3a2a;
  }
  * { margin: 0; padding: 0; box-sizing: border-box; }
  html, body { width: 1200px; height: 1000px; overflow: hidden; background: var(--page); }
  .sheet { position: relative; width: 1200px; height: 1000px; }

  .card {
    position: absolute;
    left: 266px;
    width: 664px;
    height: 397px;
    background: var(--card);
    border-radius: 22px;
    overflow: hidden;
  }
  .card--front { top: 73px; }
  .card--back { top: 533px; }

  .brand-mark {
    position: absolute;
    border-radius: 50%;
    background: var(--orange);
  }
  .card--front .brand-mark { left: 48px; top: 58px; width: 96px; height: 96px; }
  .card--back .brand-mark { left: 60px; top: 88px; width: 220px; height: 220px; }

  .brand-name,
  .brand-sub {
    position: absolute;
    font-family: "Archivo", sans-serif;
    font-stretch: 125%;
    font-weight: 800;
    color: var(--white);
    line-height: 1;
    white-space: nowrap;
  }
  .brand-sub { letter-spacing: 2px; }

  .card--front .brand-name { left: 157px; top: 88px; font-size: 30px; }
  .card--front .brand-sub { left: 158px; top: 125px; font-size: 13px; }

  .card--back .brand-name { left: 350px; top: 170px; font-size: 30px; }
  .card--back .brand-sub { left: 351px; top: 210px; font-size: 15px; }

  .contact {
    position: absolute;
    left: 157px;
    top: 186px;
    font-family: "Montserrat", sans-serif;
    color: var(--text);
  }
  .contact__name { font-size: 17px; font-weight: 600; color: var(--orange); margin-bottom: 16px; }
  .contact__line { display: flex; align-items: center; gap: 8px; font-size: 14px; margin-bottom: 6px; white-space: nowrap; }
  .contact__line svg { width: 13px; height: 13px; fill: var(--orange); flex: none; }
  .services { margin-top: 16px; font-size: 14px; line-height: 20px; white-space: nowrap; }

  .accent-bar {
    position: absolute;
    left: 0; bottom: 0;
    width: 100%; height: 20px;
    background: linear-gradient(90deg, var(--red), var(--amber) 48%, var(--red));
  }
</style>
</head>
<body>
<main class="sheet">
  <section class="card card--front" aria-label="Card front">
    <span class="brand-mark" aria-hidden="true"></span>
    <div class="brand-name">BRINTEL WORKS</div>
    <div class="brand-sub">PTY LTD</div>
    <div class="contact">
      <p class="contact__name">Dale Harmon</p>
      <p class="contact__line">
        <svg viewBox="0 0 24 24" aria-hidden="true"><path d="M6.6 10.8a15.1 15.1 0 0 0 6.6 6.6l2.2-2.2a1 1 0 0 1 1-.25 11.4 11.4 0 0 0 3.6.57 1 1 0 0 1 1 1V20a1 1 0 0 1-1 1A17 17 0 0 1 3 4a1 1 0 0 1 1-1h3.5a1 1 0 0 1 1 1c0 1.25.2 2.45.57 3.57a1 1 0 0 1-.25 1z"/></svg>
        07 3918 4726
      </p>
      <p class="contact__line">
        <svg viewBox="0 0 24 24" aria-hidden="true"><path d="M2 5h20v14H2z M2 5l10 8 10-8" /></svg>
        admin@brintelworks.com.au
      </p>
      <p class="services">Install all types of gas appliances &amp;<br>equipment inc. hot water units<br>Maintain / repair / replace all types of<br>gas appliances &amp; equipment</p>
    </div>
    <div class="accent-bar"></div>
  </section>

  <section class="card card--back" aria-label="Card back">
    <span class="brand-mark" aria-hidden="true"></span>
    <div class="brand-name">BRINTEL WORKS</div>
    <div class="brand-sub">PTY LTD</div>
  </section>
</main>
</body>
</html>
```